Moon Tot needs ecommerce website design help

We need someone to set up a fully functional website for us. We sell baby bibs, I attached them along with our company logo (MTG: moon tot goods). The bibs are made of 100% silicon, they are safe, light weight, soft, smooth, flexible, dishwasher safe and has funny faces.

Business name: Moon Tot Goods
Elm Hollow, NY 00000
email: MoonTotGoods@mailbox-example.com
tel.: (555) 014-TOTS
website: MoonTotGoods-example.com

Target Market(s)

18-40

Industry/Entity Type

Baby

Coding

Coded - Design and coding required

Number of Pages Required

5+ page

Requirements
Must have
• 1. Pages: Why buy from us, Contact Us, Home page, Products Page, Blog
• 2. Use the colors from our logo for the web design.
• 3. Need a link that will connect visitors to our facebook, instagram, Pinterest and Tumblr account. Would like links on,the top left side of the page
Nice to have
• My Cart page
• 1. On contact us page, we want to include some type of template for the customer to complete. (Ex: name, email address, contact number, optional home address, comments)
• 2. When clients visit our website, we want a capture/pop up for the customer to subscribe to our email list to receive discounts. (Ex. Want 10% off your next order ? Suscribe to our mailing list below and get a 10% off code to use at check out. If they don't want to subscribe, they have the option to select "No Thank You, I want to pay full price).
• 3. On home page have subscribe to our email list.

```html
<!DOCTYPE html>
<html lang="en">
<head>
<meta charset="utf-8">
<title>Moon Tot Goods</title>
<link href="https://fonts.googleapis.com/css2?family=Open+Sans:wght@400;600;700&display=swap" rel="stylesheet">
<style>
:root{
  --pink:#f0566b;
  --lime:#b5d334;
  --ink:#222;
  --dark:#1a1a1a;
  --footer:#2b2b2b;
  --text:#555;
  --white:#fff;
}
*{box-sizing:border-box;margin:0;padding:0}
html,body{width:1200px;height:2348px;overflow:hidden}
body{font-family:"Open Sans",Arial,sans-serif;color:var(--text);background:#fff;position:relative}
.topbar{height:40px;background:#3a3a3a;display:flex;align-items:center;justify-content:space-between;padding:0 28px}
.social{display:flex;gap:8px}
.social span{width:18px;height:18px;border-radius:50%;background:var(--lime);display:block}
.social span:nth-child(even){background:var(--pink)}
.topbar .contact{color:var(--pink);font-size:12px;display:flex;gap:22px}
.hero{height:560px;position:relative;background:linear-gradient(135deg,#e9ddd2 0%,#d8c6b6 45%,#f1e9e1 100%)}
.header{position:absolute;top:8px;left:0;right:0;height:48px;display:flex;align-items:center;justify-content:space-between;padding:0 28px}
.brand{display:flex;align-items:center;gap:10px;font-size:22px;font-weight:700;color:var(--pink)}
.brand i{width:28px;height:28px;border-radius:50%;background:var(--lime);display:block}
.nav{display:flex;gap:6px}
.nav a{font-size:12px;font-weight:600;color:#444;text-decoration:none;padding:8px 16px;text-transform:uppercase}
.nav a.active{background:rgba(255,255,255,.75)}
section h2{font-size:30px;font-weight:600;color:var(--ink);text-align:center;text-transform:uppercase}
section h2 em{font-style:normal;color:var(--pink)}
.lead{font-size:12px;line-height:22px;text-align:center;max-width:1100px;margin:14px auto 0}
.welcome{height:260px;padding-top:64px}
.why{height:340px;background:var(--dark);padding-top:36px}
.why h2{color:#fff}
.why .lead{color:#aaa;max-width:1040px}
.perks{position:relative;height:120px;margin-top:30px}
.perk{position:absolute;top:0;width:104px;height:104px;margin-left:-52px;border-radius:50%;background:var(--lime);display:flex;flex-direction:column;align-items:center;justify-content:center;color:var(--ink);font-size:11px;font-weight:700;text-align:center;line-height:14px}
.perk svg{margin-bottom:4px}
.products{height:600px;padding-top:70px}
.cards{position:relative;height:352px;margin-top:32px}
.card{position:absolute;top:0;width:240px;height:352px;border:8px solid var(--lime);border-top-width:14px;background:#fff;text-align:center}
.card .photo{height:170px;margin:14px 20px 0;background:radial-gradient(circle at 50% 50%,#e8c94c 0%,#f5efe0 60%,#fff 100%)}
.card h3{font-size:13px;font-weight:600;color:#333;margin-top:14px}
.card .price{font-size:17px;color:var(--pink);margin-top:8px}
.card .price s{color:#999;font-size:14px;margin-left:6px}
.card .btn{display:inline-block;margin-top:12px;background:var(--pink);color:#fff;font-size:11px;font-weight:600;padding:8px 16px;text-transform:uppercase}
.newsletter{height:220px;background:var(--pink);padding-top:56px;text-align:center}
.newsletter h2{color:#fff;font-size:26px}
.newsletter p{color:#fff;font-size:12px;margin-top:4px}
.signup{display:flex;justify-content:center;gap:14px;margin-top:22px}
.signup span{width:260px;height:40px;background:#fff;display:block;text-align:left;font-size:12px;color:#999;padding:11px 12px}
.signup b{width:170px;height:40px;background:var(--ink);color:#fff;font-size:12px;display:block;padding-top:12px}
.footer{height:280px;background:var(--footer);padding:36px 28px 0;display:grid;grid-template-columns:190px 220px 160px 1fr;gap:0 24px;color:#bbb;font-size:12px}
.footer h4{color:#fff;font-size:13px;font-weight:700;text-transform:uppercase;margin-bottom:14px}
.footer li{list-style:none;line-height:26px;display:flex;align-items:center;gap:8px}
.footer li i{width:10px;height:10px;background:var(--pink);display:block;border-radius:50%}
.post{display:flex;gap:14px;margin-bottom:18px}
.post .thumb{width:64px;height:56px;background:linear-gradient(135deg,#c9d4dc,#e6e0d8)}
.post p{line-height:18px}
.post small{color:var(--pink)}
.bottombar{height:48px;background:#1c1c1c;display:flex;align-items:center;justify-content:space-between;padding:0 28px;color:#888;font-size:11px}
.cards-pay{display:flex;gap:8px}
.cards-pay span{width:48px;height:28px;background:#eee;border-radius:3px;display:block}
.scrim{position:absolute;inset:0;background:rgba(0,0,0,.62);z-index:10}
.popup{position:absolute;left:132px;top:160px;width:928px;height:400px;background:var(--pink);border:8px solid var(--lime);z-index:20;text-align:center;padding-top:116px;color:#fff}
.popup h2{font-size:30px;font-weight:600;color:#fff;text-transform:uppercase}
.popup p{font-size:12px;margin-top:14px}
.popup .form{display:flex;justify-content:center;gap:20px;margin-top:40px}
.popup .field{width:308px;height:48px;background:#fff;color:#999;font-size:12px;text-align:left;padding:15px 12px}
.popup .submit{width:152px;height:48px;background:var(--ink);font-size:12px;font-weight:600;padding-top:15px}
.popup .decline{width:156px;height:48px;background:#333;font-size:12px;font-weight:600;padding-top:8px;line-height:15px}
.popup .decline small{display:block;font-size:9px;font-weight:400}
</style>
</head>
<body>
<div class="topbar">
  <div class="social" aria-label="Social links"><span></span><span></span><span></span><span></span></div>
  <div class="contact"><span>(555) 014-TOTS</span><span>MoonTotGoods@mailbox-example.com</span></div>
</div>

<div class="hero" role="img" aria-label="Soft photo of a baby wearing a silicone bib">
  <div class="header">
    <div class="brand"><i></i>MTG</div>
    <nav class="nav">
      <a class="active">Home</a><a>Products</a><a>Why Buy From Us</a><a>Blog</a><a>Contact Us</a>
    </nav>
  </div>
</div>

<section class="welcome">
  <h2>Welcome to <em>Moon Tot Goods</em></h2>
  <p class="lead">Our silicone bibs are made for happy mealtimes. Each one is soft, smooth and light, so little ones stay comfy from the first spoon to the last crumb. Every bib wipes clean in seconds and goes straight into the dishwasher when the day is done. We design fun faces that make babies smile and parents laugh, and we test every piece so you can feed your tot with total peace of mind.</p>
</section>

<section class="why">
  <h2>Why Buy From Us</h2>
  <p class="lead">We care about safety, comfort and easy cleaning. Our bibs catch every spill, fold flat for travel and last through many meals, so you spend less time cleaning and more time with your baby.</p>
  <div class="perks">
    <div class="perk" style="left:168px"><svg width="20" height="16" viewBox="0 0 20 16"><path d="M2 8l6 6L18 2" stroke="#222" stroke-width="3" fill="none"/></svg>100%<br>Silicone</div>
    <div class="perk" style="left:340px"><svg width="20" height="16" viewBox="0 0 20 16"><path d="M2 8l6 6L18 2" stroke="#222" stroke-width="3" fill="none"/></svg>Safe</div>
    <div class="perk" style="left:512px"><svg width="20" height="16" viewBox="0 0 20 16"><path d="M2 8l6 6L18 2" stroke="#222" stroke-width="3" fill="none"/></svg>Light<br>Weight</div>
    <div class="perk" style="left:680px"><svg width="20" height="16" viewBox="0 0 20 16"><path d="M2 8l6 6L18 2" stroke="#222" stroke-width="3" fill="none"/></svg>Soft &amp;<br>Smooth</div>
    <div class="perk" style="left:848px"><svg width="20" height="16" viewBox="0 0 20 16"><path d="M2 8l6 6L18 2" stroke="#222" stroke-width="3" fill="none"/></svg>Flexible</div>
    <div class="perk" style="left:1020px"><svg width="20" height="16" viewBox="0 0 20 16"><path d="M2 8l6 6L18 2" stroke="#222" stroke-width="3" fill="none"/></svg>Dishwasher<br>Safe</div>
  </div>
</section>

<section class="products">
  <h2>Our <em>Products</em></h2>
  <p class="lead">Pick a friendly face for every meal. All bibs come in bright colours with a deep pocket to catch food and an adjustable neck strap that grows with your baby.</p>
  <div class="cards">
    <div class="card" style="left:88px"><div class="photo" role="img" aria-label="Green silicone bib with a smiling face"></div><h3>Happy Frog Bib</h3><div class="price">$18.99<s>$24.99</s></div><span class="btn">Add to Cart</span></div>
    <div class="card" style="left:360px"><div class="photo" role="img" aria-label="Orange silicone bib with a tiger face"></div><h3>Tiny Tiger Bib</h3><div class="price">$18.99<s>$24.99</s></div><span class="btn">Add to Cart</span></div>
    <div class="card" style="left:632px"><div class="photo" role="img" aria-label="Blue silicone bib with a funny face"></div><h3>Blue Buddy Bib</h3><div class="price">$18.99<s>$24.99</s></div><span class="btn">Add to Cart</span></div>
    <div class="card" style="left:904px"><div class="photo" role="img" aria-label="Yellow silicone bib with a cheerful face"></div><h3>Sunny Chick Bib</h3><div class="price">$18.99<s>$24.99</s></div><span class="btn">Add to Cart</span></div>
  </div>
</section>

<section class="newsletter">
  <h2>Signup Our Newsletter</h2>
  <p>Get news and offers</p>
  <div class="signup"><span>Your Name</span><span>Your Email</span><b>SUBMIT</b></div>
</section>

<footer class="footer">
  <div><h4>Links</h4><ul><li>Home</li><li>Products</li><li>Why Buy From Us</li><li>Blog</li><li>Contact Us</li></ul></div>
  <div><h4>Contact</h4><ul><li><i></i>Elm Hollow, NY 00000</li><li><i></i>MoonTotGoods@mailbox-example.com</li><li><i></i>(555) 014-TOTS</li><li><i></i>MoonTotGoods-example.com</li></ul></div>
  <div><h4>Follow Us</h4><ul><li><i></i>Friends Page</li><li><i></i>Photo Feed</li><li><i></i>Pin Boards</li><li><i></i>Short Posts</li></ul></div>
  <div><h4>Blog</h4>
    <div class="post"><div class="thumb" role="img" aria-label="Blog photo of a mealtime"></div><p>Easy tips for calm first meals<br><small>June 12, 2016</small></p></div>
    <div class="post"><div class="thumb" role="img" aria-label="Blog photo of baby gear"></div><p>How to clean silicone bibs fast<br><small>June 04, 2016</small></p></div>
  </div>
</footer>

<div class="bottombar">
  <span>Copyright © 2016 Moon Tot Goods. All rights reserved.</span>
  <div class="cards-pay" aria-label="Accepted payment cards"><span></span><span></span><span></span><span></span></div>
</div>

<div class="scrim"></div>
<div class="popup">
  <h2>Want 10% off your next order ?</h2>
  <p>Subscribe to our mailing list below and get a 10% off code to use at check out.</p>
  <div class="form">
    <div class="field">Enter Your Email Address</div>
    <div class="submit">SUBMIT</div>
    <div class="decline">NO THANK YOU<small>I want to pay full price</small></div>
  </div>
</div>
</body>
</html>
```